Business Card Design - Photographer

I am a landscape photographer and I require a business card design. 

I require two designs:
1)  a double sided business card
 and
b)  a single sided business card 

The single sided design can either be the same as the double sided (with just one side having all the information)....or it can be an entire new design. Its up to you.

My corporate colours are (CMYK):

Blue   69, 32, 0, 0
Grey  72,  64,  47,  31
Green  32,  2,  91,  0
Yellow   0, 19, 92, 0
Orange  0, 39, 75, 0

Colour space in final file should be in CMYK.

The details that need to be included on the card:

- Use the provided Logo
- Name: Wiktor Baranowski
- Email:   sales@vistalumeworks.com.au
- Website:    vistalumeworks.com.au
- Twitter:    twitter.com/vistalumeworks
- Facebook:   facebook.com/vistalumeworks
- Mobile  0417 539 662

Please use the attached template to design the logo to the specified size, including the marked bleed lines. I have also attached my logo in PNG (transparent background) and ai format for you to use.

The final file should be:
- Photoshop version with layers so I can edit the name/text etc. All non vector files should be high resolution at 1039 x 697 pixels at 300 dpi.

I also require a file as:
- Vector based PDF

Anyway questions please contact me.

Thank you

Industry/Entity Type

Landscape

Logo styles of interest
Pictorial/Combination Logo
Abstract Logo
Wordmark Logo
Lettermark Logo
Requirements
Must have
• The details that need to be included on the card:

- Use the provided Logo
- Name: Wiktor Baranowski
- Email: sales@vistalumeworks.com.au
- Website: vistalumeworks.com.au
- Twitter: twitter.com/vistalumeworks
- Facebook: facebook.com/vistalumeworks
- Mobile 0417 539 662

```html
<!DOCTYPE html>
<html lang="en">
<head>
<meta charset="utf-8">
<title>Wiktor Baranowski – Business Card</title>
<link rel="stylesheet" href="https://fonts.googleapis.com/css2?family=Cinzel:wght@500&family=Open+Sans:wght@400&display=swap">
<style>
  :root {
    --backdrop: #ecebe8;
    --card-white: #ffffff;
    --brand-blue: #3f8bcb;
    --brand-grey: #3b4257;
    --text-dark: #3b4257;
    --text-light: #ffffff;
  }
  * { box-sizing: border-box; margin: 0; padding: 0; }
  html, body { width: 1200px; height: 400px; overflow: hidden; background: var(--backdrop); }
  .canvas { position: relative; width: 1200px; height: 400px; }

  .card {
    position: absolute; top: 48px; width: 526px; height: 300px;
    border-radius: 22px; overflow: hidden;
    box-shadow: 0 2px 6px rgba(0,0,0,0.18);
  }
  .card--front { left: 45px; background: var(--card-white); }
  .card--back { left: 617px; background: var(--brand-blue); }
  .card__shapes { position: absolute; inset: 0; }

  .brand { position: absolute; height: 190px; }
  .brand > * { position: absolute; left: 50%; transform: translateX(-50%); white-space: nowrap; }
  .brand__dot { width: 84px; height: 84px; border-radius: 50%; background: var(--brand-grey); }
  .brand__name {
    font-family: "Cinzel", serif; font-weight: 500; font-size: 22px; line-height: 26px;
    color: var(--brand-grey); letter-spacing: 0.3px;
  }
  .brand__rule { width: 250px; height: 1px; background: var(--brand-grey); }
  .brand__tagline {
    font-family: "Cinzel", serif; font-weight: 500; font-size: 9.5px; line-height: 12px;
    color: var(--brand-grey); letter-spacing: 2px;
  }

  .card--front .brand { left: 0; width: 338px; top: 24px; }
  .card--front .brand__dot { top: 0; }
  .card--front .brand__name { top: 100px; }
  .card--front .brand__rule { top: 128px; }
  .card--front .brand__tagline { top: 134px; }

  .card--back .brand { left: 0; right: 0; top: 47px; }
  .card--back .brand__dot { top: 0; }
  .card--back .brand__name { top: 120px; }
  .card--back .brand__rule { top: 148px; }
  .card--back .brand__tagline { top: 154px; }

  .social { position: absolute; left: 47px; top: 187px; list-style: none;
    font-family: "Open Sans", sans-serif; font-size: 13px; color: var(--text-dark); }
  .social li { display: flex; align-items: center; height: 20px; }
  .social__mark { width: 9px; height: 9px; margin-right: 8px; background: var(--brand-blue); border-radius: 1px; }
  .social li:nth-child(2) .social__mark { background: #3b5a98; }

  .contact { position: absolute; right: 18px; top: 174px; list-style: none;
    font-family: "Open Sans", sans-serif; font-size: 13px; color: var(--text-light); text-align: right; }
  .contact li { display: flex; justify-content: flex-end; align-items: center; height: 20px; }
  .contact__icon { width: 12px; height: 12px; margin-left: 10px; }
  .contact__icon--none { visibility: hidden; }
  .contact .contact__gap { height: 12px; }

  .website { position: absolute; left: 0; right: 0; top: 244px; text-align: center;
    font-family: "Open Sans", sans-serif; font-size: 13px; letter-spacing: 2px; color: var(--text-light); }
</style>
</head>
<body>
<main class="canvas">

  <section class="card card--front" aria-label="Card front">
    <svg class="card__shapes" viewBox="0 0 526 300" preserveAspectRatio="none" aria-hidden="true">
      <path d="M0,240 C150,290 360,245 526,16 L526,300 L0,300 Z" fill="var(--brand-blue)"/>
      <path d="M0,222 C110,292 280,262 370,166 C290,250 120,282 0,246 Z" fill="var(--brand-grey)"/>
    </svg>

    <div class="brand">
      <span class="brand__dot"></span>
      <span class="brand__name">WIKTOR BARANOWSKI</span>
      <span class="brand__rule"></span>
      <span class="brand__tagline">FINE ART PHOTOGRAPHY</span>
    </div>

    <ul class="social">
      <li><span class="social__mark"></span>vistalumeworks</li>
      <li><span class="social__mark"></span>vistalumeworks</li>
    </ul>

    <ul class="contact">
      <li>00, Complex Name<span class="contact__icon contact__icon--none"></span></li>
      <li>State Name, City 0020<span class="contact__icon contact__icon--none"></span></li>
      <li class="contact__gap"></li>
      <li>0417 539 662
        <svg class="contact__icon" viewBox="0 0 12 12" aria-hidden="true"><rect x="3.5" y="1" width="5" height="10" rx="1" fill="none" stroke="#fff" stroke-width="1.3"/><circle cx="6" cy="9" r="0.8" fill="#fff"/></svg>
      </li>
      <li>sales@vistalumeworks.com.au
        <svg class="contact__icon" viewBox="0 0 12 12" aria-hidden="true"><rect x="1.5" y="3" width="9" height="6" fill="#fff"/><path d="M1.5,3 L6,6.5 L10.5,3" fill="none" stroke="var(--brand-blue)" stroke-width="0.8"/></svg>
      </li>
      <li>www.vistalumeworks.com.au
        <svg class="contact__icon" viewBox="0 0 12 12" aria-hidden="true"><circle cx="6" cy="6" r="4.5" fill="#fff"/></svg>
      </li>
    </ul>
  </section>

  <section class="card card--back" aria-label="Card back">
    <div class="brand">
      <span class="brand__dot"></span>
      <span class="brand__name">WIKTOR BARANOWSKI</span>
      <span class="brand__rule"></span>
      <span class="brand__tagline">FINE ART PHOTOGRAPHY</span>
    </div>
    <p class="website">www.vistalumeworks.com.au</p>
  </section>

</main>
</body>
</html>
```